Landscape Construction and Design Company

We are a landscape construction and design company from New Jersey. We design and install landscapes and hardscapes for residential properties. The name of the company is Belwick's Landscape and Design LLC. We specialize mostly in planting trees and stone work, some water features. We would like to see design themes that include a tree or trees and a stone walkway or wall. We like earth tone colors. We like traditional to modern designs.

Target Market(s)

Homeowners

Industry/Entity Type

Landscape

Contact Information for Business Card

Nature themed design, earth tone colors, space for company name, address, phone numbers, email and website address

Logo Text

No text

Font styles to use
Serif

Colors

Designer to choose colors to be used in the design.

Requirements
Must have
• A tree or trees, similar to the ones uploaded in my supporting images
Nice to have
• I like trees similar to those in my uploaded supporting images. I like artistic, nature theme, earth tone colors
Should not have
• Pictures of real landscapes, cartoon looking logo or objects

```html
<!DOCTYPE html>
<html lang="en">
<head>
<meta charset="utf-8">
<title>Belwick's Landscape and Design LLC – Business Card</title>
<link rel="stylesheet" href="https://fonts.googleapis.com/css2?family=Cinzel:wght@600&family=Lato:wght@400;700&display=swap">
<style>
  :root {
    --canvas-bg: #ecebe7;
    --card-dark: #2a2a2a;
    --card-light: #ffffff;
    --leaf-green: #67a22d;
    --bark-maroon: #70282a;
    --ink: #2c2c2c;
    --on-dark: #f4f4f4;
  }
  * { box-sizing: border-box; margin: 0; padding: 0; }
  html, body { width: 1200px; height: 900px; overflow: hidden; }
  body { background: var(--canvas-bg); position: relative; font-family: "Lato", sans-serif; }

  .card {
    position: absolute;
    width: 700px; height: 400px;
    overflow: hidden;
    box-shadow: 0 4px 14px rgba(0,0,0,.18);
  }

  /* Front */
  .card-front { left: 90px; top: 45px; background: var(--card-dark); }
  .brand {
    position: absolute; left: 0; right: 0; top: 135px;
    display: flex; align-items: center; justify-content: center; gap: 18px;
  }
  .brand-dot { width: 44px; height: 44px; border-radius: 50%; background: var(--leaf-green); flex: none; }
  .brand-name {
    font-family: "Lato", sans-serif; font-weight: 400; font-size: 30px;
    color: var(--leaf-green); line-height: 1;
  }
  .services {
    position: absolute; left: 0; right: 0; bottom: 72px; text-align: center;
    color: var(--on-dark); font-size: 17px; letter-spacing: 1px; text-transform: uppercase;
  }

  /* Back */
  .card-back { left: 410px; top: 470px; background: var(--card-light); }
  .person { position: absolute; left: 44px; top: 52px; }
  .person-name {
    font-family: "Cinzel", serif; font-weight: 600; font-size: 27px;
    color: var(--leaf-green); letter-spacing: 1px;
  }
  .person-role { font-size: 17px; color: var(--ink); margin-top: 2px; }
  .contacts { position: absolute; left: 44px; top: 158px; list-style: none; color: var(--ink); font-size: 17px; }
  .contacts li { display: flex; align-items: center; gap: 9px; line-height: 25px; }
  .contacts svg { width: 15px; height: 15px; fill: var(--leaf-green); flex: none; }
  .contacts .address { display: block; margin-top: 10px; line-height: 24px; }
  .accent-rule {
    position: absolute; left: 0; right: 0; bottom: 84px; height: 6px;
    background: var(--bark-maroon);
  }
  .base-band {
    position: absolute; left: 0; right: 0; bottom: 0; height: 76px;
    background: var(--leaf-green);
  }
</style>
</head>
<body>

<section class="card card-front">
  <div class="brand">
    <span class="brand-dot"></span>
    <h1 class="brand-name">Belwick's Landscape and Design LLC</h1>
  </div>
  <p class="services">Planting Trees | Stone Work | Water Features</p>
</section>

<section class="card card-back">
  <div class="person">
    <h2 class="person-name">Marcus Hale</h2>
    <p class="person-role">Managing Director</p>
  </div>

  <ul class="contacts">
    <li><svg viewBox="0 0 16 16"><path d="M3 1h3l1.5 4-2 1.3a9 9 0 0 0 4.2 4.2L11 8.5l4 1.5v3a2 2 0 0 1-2 2A13 13 0 0 1 1 3a2 2 0 0 1 2-2z"/></svg>201 555 0147</li>
    <li><svg viewBox="0 0 16 16"><path d="M1 3h14v10H1z M1 3l7 6 7-6" stroke="#fff" stroke-width="1.2"/></svg>info@belwickslandscape.com</li>
    <li><svg viewBox="0 0 16 16"><circle cx="8" cy="8" r="7"/><path d="M1 8h14M8 1c3 3 3 11 0 14M8 1c-3 3-3 11 0 14" stroke="#fff" stroke-width="1" fill="none"/></svg>www.belwickslandscape.com</li>
    <li class="address">88 Orchard Lane,<br>Montclair, NJ 07042</li>
  </ul>

  <div class="accent-rule"></div>
  <div class="base-band"></div>
</section>

</body>
</html>
```